Clear sticker design for packaging

I need 4” diameter clear stickers designed for birthdays, thank you , teachers day and all the other special days to complete my gift packaging. They will go on the top of each tube to differentiate each gift for each occasion. Our design is on craft paper and I’ve uploaded a few examples of what we are trying to achieve. Last picture is the top of our tube where the stickers will be placed. We don’t want too much color unless for Christmas and Valentine’s Day maybe! We are working with black and gold or a mixture of both mostly

```html
<!DOCTYPE html>
<html lang="en">
<head>
<meta charset="utf-8">
<title>Thank You Sticker</title>
<link rel="stylesheet" href="https://fonts.googleapis.com/css2?family=Amatic+SC:wght@700&family=Great+Vibes&display=swap">
<style>
  :root {
    --paper: #ffffff;
    --ink: #1c1a18;
    --gold: #d9bd5a;
    --gold-soft: #e8d48c;
    --sand-light: #efe6dc;
    --sand-dark: #e2d3c3;
    --taupe: #6f6459;
    --leaf-tone: #f3eee6;
  }
  html, body {
    margin: 0;
    padding: 0;
    width: 1200px;
    height: 2444px;
    overflow: hidden;
    background: var(--paper);
  }
  .sticker {
    display: block;
    width: 1200px;
    height: 2444px;
  }
  .blob-light { fill: var(--sand-light); }
  .blob-dark { fill: var(--sand-dark); opacity: .85; }
  .frame-ring { fill: none; stroke: var(--gold); stroke-width: 4; stroke-linecap: round; }
  .swash { fill: none; stroke: var(--ink); stroke-width: 7; stroke-linecap: round; }
  .title-shadow {
    font-family: "Amatic SC", "Arial Narrow", sans-serif;
    font-weight: 700;
    font-size: 250px;
    fill: var(--gold-soft);
    stroke: var(--gold);
    stroke-width: 10;
    stroke-linejoin: round;
  }
  .title {
    font-family: "Amatic SC", "Arial Narrow", sans-serif;
    font-weight: 700;
    font-size: 250px;
    fill: var(--ink);
  }
  .script {
    font-family: "Great Vibes", cursive;
    font-size: 150px;
    fill: var(--ink);
  }
  .dot { fill: var(--gold); }
  .bubble { fill: none; stroke: var(--taupe); stroke-width: 4; }
  .leaf-art { fill: var(--leaf-tone); }
</style>
</head>
<body>
<svg class="sticker" viewBox="100 1330 1000 1000" xmlns="http://www.w3.org/2000/svg">
  <g class="backdrop">
    <path class="blob-light" d="M360,1450 C450,1395 600,1382 700,1390 C900,1410 1060,1600 1065,1850 C1066,1930 1055,1970 1040,1995 C1000,1800 950,1620 850,1520 C760,1495 620,1505 520,1502 C440,1500 390,1482 360,1450 Z"/>
    <path class="blob-dark" d="M820,1462 C930,1510 1060,1650 1065,1850 C1066,1930 1055,1970 1040,1995 C1000,1850 975,1720 905,1640 C835,1560 812,1505 820,1462 Z"/>
  </g>

  <path class="frame-ring" d="M218,2030 A420,420 0 1 1 640,2270"/>

  <path class="swash" d="M185,1895 C265,1895 320,1985 400,1982 C470,1980 500,1950 520,1925 M660,1935 C700,1970 760,1950 830,1920 C900,1890 960,1900 1010,1935"/>

  <g class="headline">
    <text class="title-shadow" x="598" y="1866" text-anchor="middle" letter-spacing="14">THANK</text>
    <text class="title" x="590" y="1858" text-anchor="middle" letter-spacing="14">THANK</text>
    <text class="script" x="585" y="1975" text-anchor="middle">you</text>
  </g>

  <g class="confetti">
    <circle class="dot" cx="192" cy="1675" r="4"/>
    <circle class="dot" cx="222" cy="1790" r="7"/>
    <circle class="dot" cx="143" cy="1843" r="4"/>
    <circle class="dot" cx="288" cy="1860" r="6"/>
    <circle class="dot" cx="343" cy="1923" r="10"/>
    <circle class="dot" cx="742" cy="2112" r="4"/>
    <circle class="dot" cx="862" cy="2092" r="4"/>
    <circle class="dot" cx="928" cy="2088" r="7"/>
    <circle class="dot" cx="790" cy="2178" r="9"/>
    <circle class="dot" cx="835" cy="2222" r="4"/>
    <circle class="dot" cx="685" cy="2298" r="4"/>
  </g>

  <g class="bubbles">
    <ellipse class="bubble" cx="575" cy="2148" rx="10" ry="6"/>
    <ellipse class="bubble" cx="661" cy="2140" rx="20" ry="11"/>
    <ellipse class="bubble" cx="559" cy="2194" rx="20" ry="10"/>
    <ellipse class="bubble" cx="712" cy="2193" rx="14" ry="8"/>
    <ellipse class="bubble" cx="622" cy="2224" rx="16" ry="10"/>
  </g>

  <rect class="leaf-art" x="205" y="2035" width="350" height="265" rx="60" role="img" aria-label="Line drawing of leafy sprigs in dark brown with a gold offset outline"/>
</svg>
</body>
</html>
```